Electric mountain bike tours nz

We are an Electric Mountain bike tour company in New Zealand. We will be offering bike rental and guided tours around the Nelson region in New Zealand. I want our website to represent both Mountain biking and New Zealand with the colours layout and features. We want tabs for the following:
-1 about us
-2 what we offer
-3 bookings/contact
Under the about us tab will be who we are as a a company. I want the ability to add videos to each of these tabs as we move foward with videos of the tracks we will be riding. I want the website to be editable so I can add and remove videos/photos myself. Also "our bikes" will be under this tab.
Under the what we offer tab will be
-1 bike rental and pricing
-2 guided tours and pricing
-3 recommended package deals.
I want to able to put the tracks under the guided tours tab and select beginner/ intermediate/advanced and have the tracks in each of the following to match the rider level. Also to be able to have a small video of the track would be great in this section.
Bookings and contact tab
(Further information for this tab to be updated soon)
Coded - Design and coding required
1 page
- Silver ferns, kiwi, mountains

```html
<!DOCTYPE html>
<html lang="en">
<head>
<meta charset="utf-8">
<title>RIDGEVOLT – Electric Mountain Bike Tours in New Zealand</title>
<link href="https://fonts.googleapis.com/css2?family=Nunito:ital,wght@0,600;0,700;0,800;1,700;1,800&family=Open+Sans:wght@400;600;700&display=swap" rel="stylesheet">
<style>
:root{
  --white:#ffffff;
  --ink:#222222;
  --muted:#555555;
  --blue:#1e9be8;
  --blue-deep:#1a5fe0;
  --green:#1f9a2a;
  --green-dark:#1c6f25;
  --green-btn:#1f7a2c;
  --orange:#f58a3c;
  --orange-dark:#ef6a16;
  --royal:#3d64c8;
  --royal-dark:#2848b4;
  --card:#272727;
  --card-line:#3a3a3a;
  --footer:#e4e4e4;
  --fern:#f1f1f1;
  --kiwi:#b49a78;
}
*{margin:0;padding:0;box-sizing:border-box}
html,body{width:1200px;height:3186px;overflow:hidden}
body{position:relative;background:var(--white);font-family:"Open Sans",Arial,sans-serif;color:var(--ink)}
.abs{position:absolute}
.heading{font-family:"Nunito",Arial,sans-serif;font-weight:700;letter-spacing:1px}
.btn{position:absolute;display:flex;align-items:center;justify-content:center;border-radius:24px;color:var(--white);font-family:"Nunito",Arial,sans-serif;font-weight:700;font-size:18px}
.btn-blue{background:linear-gradient(90deg,var(--blue-deep),var(--blue))}

/* header */
.site-header{position:absolute;left:0;top:0;width:1200px;height:94px;background:var(--white);z-index:5}
.nav{position:absolute;top:48px;left:0;font-family:"Open Sans",Arial,sans-serif;font-weight:700;font-size:12.5px;color:var(--ink)}
.nav span{position:absolute;white-space:nowrap}
.brand-badge{position:absolute;left:187px;top:2px;width:156px;height:156px;border-radius:50%;background:var(--white);z-index:6;display:flex;align-items:center;justify-content:center}
.brand-name{font-family:"Nunito",Arial,sans-serif;font-weight:800;font-size:24px;color:var(--ink);letter-spacing:1px}

/* hero */
.hero{position:absolute;left:0;top:94px;width:1200px;height:640px;background:linear-gradient(180deg,#8fa2b8 0%,#c9c4b2 30%,#6e7552 60%,#3d3f2a 100%)}
.hero-title{position:absolute;left:0;top:210px;width:1210px;text-align:center;color:var(--white);font-family:"Nunito",Arial,sans-serif;font-weight:800;font-size:40px;line-height:44px;letter-spacing:1px}
.hero-dots{position:absolute;left:1074px;top:232px}
.hero-dots i{display:block;width:11px;height:11px;border-radius:50%;background:var(--white);margin-bottom:10px}
.hero-dots i.on{background:transparent;border:2px solid var(--white)}

/* about */
.about{position:absolute;left:0;top:700px;width:1200px;height:480px;z-index:3}
.fern{position:absolute;background:var(--fern);border-radius:50% 50% 50% 50% / 60% 60% 40% 40%}
.section-title{position:absolute;left:0;width:1210px;text-align:center;font-family:"Nunito",Arial,sans-serif;font-weight:700;color:var(--ink)}
.about-copy{position:absolute;left:300px;width:610px;text-align:center;font-size:12.5px;line-height:21px;color:var(--muted)}

/* video */
.video-band{position:absolute;left:0;top:1170px;width:1200px;height:495px;background:linear-gradient(135deg,#2aa534 0%,#1a8d22 50%,#23a02d 100%)}
.video-copy{position:absolute;left:208px;top:195px;width:350px;font-size:12.5px;line-height:24px;color:var(--white)}
.btn-outline{border:2px solid var(--white);background:transparent}
.video-frame{position:absolute;left:573px;top:107px;width:466px;height:282px;background:linear-gradient(160deg,#6f6f6f,#3a3a3a 60%,#262626)}

/* packages */
.packages{position:absolute;left:0;top:1657px;width:1200px;height:840px;background:linear-gradient(180deg,#f4f6f9 0%,#dfe4ec 40%,#a8b3c2 75%,#8e98a8 100%)}
.tabs{position:absolute;top:163px;left:0;font-size:10.5px;font-weight:600;color:var(--ink)}
.tabs span{position:absolute;white-space:nowrap}
.tabs .active{background:var(--ink);color:var(--white);padding:2px 8px}
.kiwi{position:absolute;background:var(--kiwi);border-radius:50%}
.plan{position:absolute;background:var(--card);color:var(--white);text-align:center}
.plan-head{height:44px;display:flex;align-items:center;justify-content:center;font-family:"Nunito",Arial,sans-serif;font-style:italic;font-weight:800;font-size:22px}
.plan-price{height:110px;display:flex;align-items:center;justify-content:center;font-family:"Nunito",Arial,sans-serif;font-style:italic;font-weight:800;font-size:56px;clip-path:polygon(0 0,100% 0,100% 82%,0 100%)}
.plan-price sup{font-size:22px;align-self:flex-start;margin-top:28px;margin-right:4px}
.plan-price small{font-size:12px;font-weight:600;margin-top:22px;margin-left:2px}
.plan-name{font-family:"Nunito",Arial,sans-serif;font-style:italic;font-weight:600;font-size:16px;margin-top:8px;height:56px;line-height:40px}
.plan-feature{font-size:11px;height:43px;line-height:43px;border-bottom:1px solid var(--card-line);margin:0 10px}
.plan-feature:last-of-type{border-bottom:none}
.btn-green{position:relative;display:inline-flex;margin-top:6px;background:var(--green-btn);border-radius:18px;width:104px;height:32px;align-items:center;justify-content:center;font-size:12px;font-weight:700}
.starter .plan-head{background:var(--orange-dark)}
.starter .plan-price{background:var(--orange)}
.standard .plan-head{background:var(--green-dark)}
.standard .plan-price{background:var(--green)}
.ultimate .plan-head{background:var(--royal-dark)}
.ultimate .plan-price{background:var(--royal)}

/* booking */
.booking{position:absolute;left:0;top:2440px;width:1200px;height:580px;background:linear-gradient(90deg,#121510 0%,#1d2418 40%,#3b4630 70%,#2a3122 100%)}
.booking-copy{position:absolute;left:217px;width:380px;font-size:12.5px;line-height:21px;color:#d6d6d6}

/* footer */
.site-footer{position:absolute;left:0;top:3005px;width:1200px;height:181px;background:linear-gradient(180deg,#d9d9d9,var(--footer))}
.footer-nav{position:absolute;top:70px;left:0;font-size:13px;color:var(--ink)}
.footer-nav span{position:absolute;white-space:nowrap}
.social{position:absolute;top:65px;width:28px;height:28px;border-radius:50%;background:var(--ink)}
</style>
</head>
<body>

<header class="site-header">
  <nav class="nav">
    <span style="left:549px">HOME</span>
    <span style="left:615px">ABOUT US</span>
    <span style="left:706px">WHAT WE OFFER</span>
    <span style="left:834px">BOOKINGS</span>
    <span style="left:925px">CONTACT US</span>
  </nav>
</header>
<div class="brand-badge"><span class="brand-name">RIDGEVOLT</span></div>

<section class="hero">
  <div class="abs" role="img" aria-label="Rider drinking beside an electric mountain bike on a hilltop overlooking the sea in New Zealand" style="inset:0"></div>
  <h1 class="hero-title">ELECTRIC MOUNTAIN<br>BIKE TOURS IN NEW ZEALAND</h1>
  <div class="btn" style="left:520px;top:312px;width:166px;height:40px;background:var(--blue);font-size:17px">Click here</div>
  <div class="hero-dots"><i class="on"></i><i></i><i></i><i></i></div>
</section>

<svg class="abs" style="left:0;top:610px;z-index:2" width="1200" height="130" viewBox="0 0 1200 130" aria-hidden="true">
  <path fill="#ffffff" d="M0 110 L60 100 L120 106 L170 92 L230 100 L300 88 L360 80 L420 86 L480 70 L540 60 L600 72 L640 54 L700 24 L740 40 L780 30 L830 50 L880 44 L930 62 L980 58 L1030 72 L1080 68 L1130 80 L1200 76 L1200 130 L0 130 Z"/>
</svg>

<section class="about">
  <div class="fern" role="img" aria-label="Faint silver fern decoration" style="left:90px;top:40px;width:170px;height:430px;transform:rotate(38deg)"></div>
  <div class="fern" role="img" aria-label="Faint silver fern decoration" style="left:990px;top:250px;width:110px;height:260px;transform:rotate(-55deg)"></div>
  <svg class="abs" style="left:563px;top:25px" width="84" height="34" viewBox="0 0 84 34" aria-hidden="true">
    <path d="M0 34 L30 6 L42 18 L54 0 L84 34 L72 34 L54 14 L42 28 L30 16 L12 34 Z" fill="#1e9be8"/>
  </svg>
  <h2 class="section-title" style="top:60px;font-size:34px">ABOUT US</h2>
  <p class="about-copy" style="top:125px">mi quis lacus mollis aliquam vvscelerisque mi tortor at ipsum cligula augue bibendum accumsan vestibulum ut commodo a mi Morbi ornare gravida elit Integer congue</p>
  <p class="about-copy" style="top:178px">Aapsum dui aliquet felis at cursus magna nisi nec elit Praesent elementum elit at tellus nec ultricies sit amet porttitor mattis enim in massa libero interdum nec interdum vel blandit sed nulla In ullam-corper est eget tempor cursus neque mi consectetuer mi a ultricies massa est sed nisl Class aptent taciti sociosqu ad litora torquent per conubia nostra per incepto</p>
  <div class="btn btn-blue" style="left:522px;top:300px;width:166px;height:44px">Read More</div>
</section>

<section class="video-band">
  <div class="abs" role="img" aria-label="Green tinted mountain landscape" style="inset:0"></div>
  <svg class="abs" style="left:208px;top:100px" width="90" height="36" viewBox="0 0 90 36" aria-hidden="true">
    <path d="M0 36 L32 6 L45 19 L58 0 L90 36 L77 36 L58 14 L45 30 L32 17 L13 36 Z" fill="#ffffff"/>
  </svg>
  <h2 class="abs heading" style="left:204px;top:137px;font-size:26px;color:var(--white)">WATCH OUR VIDEO</h2>
  <p class="video-copy">penatibus et magnis dis parturient montes nascetur ridiculus mus in iaculis facilisis massa Etiam Suspendisse quam leo molestie sed luctus quis feugiat in pede Fusce tellus Sed metus augue convallis et vehicula ut pulvinar eu ante Integer orci tellus</p>
  <div class="btn btn-outline" style="left:208px;top:334px;width:170px;height:44px">Click here</div>
  <svg class="abs" style="left:556px;top:92px" width="500" height="312" viewBox="0 0 500 312" aria-hidden="true">
    <path d="M5 75 L5 5 L75 5" fill="none" stroke="#ffffff" stroke-width="3"/>
    <path d="M493 230 L493 305 L418 305" fill="none" stroke="#ffffff" stroke-width="3"/>
  </svg>
  <div class="video-frame" role="img" aria-label="Video still of electric mountain bikes lined up in a workshop"></div>
  <svg class="abs" style="left:765px;top:203px" width="80" height="80" viewBox="0 0 80 80" aria-hidden="true">
    <circle cx="40" cy="40" r="37" fill="rgba(0,0,0,.25)" stroke="#ffffff" stroke-width="4"/>
    <path d="M32 24 L56 40 L32 56 Z" fill="#ffffff"/>
  </svg>
</section>
<svg class="abs" style="left:0;top:1160px;z-index:3" width="1200" height="26" viewBox="0 0 1200 26" aria-hidden="true">
  <path fill="#ffffff" d="M0 0 H1200 V14 L1140 18 L1080 12 L1010 20 L950 13 L880 19 L820 12 L760 18 L690 11 L620 19 L560 12 L490 18 L420 13 L350 20 L280 12 L210 19 L140 13 L70 20 L0 14 Z"/>
</svg>
<svg class="abs" style="left:0;top:1648px;z-index:2" width="1200" height="24" viewBox="0 0 1200 24" aria-hidden="true">
  <path fill="#f4f6f9" d="M0 24 H1200 V10 L1130 6 L1060 12 L990 5 L920 11 L850 6 L780 12 L710 5 L640 11 L570 6 L500 12 L430 5 L360 11 L290 6 L220 12 L150 5 L80 11 L0 6 Z"/>
</svg>

<section class="packages">
  <div class="abs" role="img" aria-label="Snow covered mountain range" style="inset:0"></div>
  <svg class="abs" style="left:563px;top:43px" width="84" height="32" viewBox="0 0 84 32" aria-hidden="true">
    <path d="M0 32 L30 5 L42 17 L54 0 L84 32 L72 32 L54 13 L42 27 L30 15 L12 32 Z" fill="#8a8a8a"/>
  </svg>
  <h2 class="section-title" style="top:78px;font-size:28px">OUR PACKAGE</h2>
  <div class="tabs">
    <span style="left:443px;top:2px">BIKE RENTAL</span>
    <span style="left:545px;top:2px">GUIDED TOURS</span>
    <span class="active" style="left:652px">RECOMMENDED</span>
  </div>
  <div class="kiwi" role="img" aria-label="Kiwi bird perched on the pricing card" style="left:172px;top:160px;width:72px;height:84px"></div>

  <div class="plan starter" style="left:178px;top:244px;width:277px;height:512px">
    <div class="plan-head">STARTER</div>
    <div class="plan-price"><sup>$</sup>19<small>/ MONTH</small></div>
    <div class="plan-name">SINGLE PLACE TRAVEL</div>
    <div class="plan-feature">Lorem ipsum doloret</div>
    <div class="plan-feature">At vero eos et accusamus</div>
    <div class="plan-feature">Nam libero tempore coluta</div>
    <div class="plan-feature">Excepteur sint occaecat</div>
    <div class="plan-feature">On the other had enounce</div>
    <div class="btn-green">BOOK NOW</div>
  </div>
  <div class="plan standard" style="left:455px;top:216px;width:278px;height:570px">
    <div class="plan-head" style="height:50px">STANDARD</div>
    <div class="plan-price"><sup>$</sup>39<small>/ MONTH</small></div>
    <div class="plan-name" style="margin-top:18px">THREE PLACE TRAVEL</div>
    <div class="plan-feature">Nam libero tempore coluta</div>
    <div class="plan-feature">On the other had enounce</div>
    <div class="plan-feature">Lorem ipsum doloret</div>
    <div class="plan-feature">At vero eos et accusamus</div>
    <div class="plan-feature">Excepteur sint occaecat</div>
    <div class="btn-green" style="margin-top:18px">BOOK NOW</div>
  </div>
  <div class="plan ultimate" style="left:733px;top:244px;width:280px;height:512px">
    <div class="plan-head">ULTIMATE</div>
    <div class="plan-price"><sup>$</sup>59<small>/ MONTH</small></div>
    <div class="plan-name">FIVE PLACE TRAVEL</div>
    <div class="plan-feature">Excepteur sint occaecat</div>
    <div class="plan-feature">Nam libero tempore coluta</div>
    <div class="plan-feature">At vero eos et accusamus</div>
    <div class="plan-feature">On the other had enounce</div>
    <div class="plan-feature">Lorem ipsum doloret</div>
    <div class="btn-green">BOOK NOW</div>
  </div>
</section>

<section class="booking">
  <div class="abs" role="img" aria-label="Orange electric mountain bike on a forest trail beside a track marker" style="inset:0"></div>
  <h2 class="abs heading" style="left:217px;top:222px;font-size:31px;color:var(--white)">OUR BOOKING</h2>
  <p class="booking-copy" style="top:270px">Arnare gravida elit Integer congue augue et malesuada iaculis ipsum dui aliquet felis at cursus ma</p>
  <p class="booking-copy" style="top:330px;color:#bdbdbd">libero interdum nec interdum vel blandit sed nulla In ullamcor-per est eget tempor cursus neque mi consectetuer mi a ultri-cies massa est sed nisl Class aptent taciti sociosqu ad litora torquent per conubia nostra per</p>
  <div class="btn btn-blue" style="left:217px;top:446px;width:167px;height:44px">Read More</div>
</section>
<svg class="abs" style="left:0;top:2440px;z-index:2" width="1200" height="150" viewBox="0 0 1200 150" aria-hidden="true">
  <path fill="#8e98a8" d="M0 0 H1200 V146 L1150 142 L1140 90 L1080 104 L1050 80 L1000 92 L960 70 L920 88 L880 60 L840 76 L800 52 L760 70 L720 58 L680 78 L640 66 L600 82 L560 74 L520 90 L470 80 L420 96 L370 88 L320 102 L270 94 L220 110 L160 104 L100 118 L40 114 L0 126 Z"/>
</svg>
<div class="kiwi" role="img" aria-label="Kiwi bird standing on the ridge" style="left:1035px;top:2410px;width:110px;height:120px;z-index:3"></div>

<footer class="site-footer">
  <svg class="abs" style="left:0;top:-16px" width="1200" height="30" viewBox="0 0 1200 30" aria-hidden="true">
    <path fill="#d9d9d9" d="M0 30 V12 L80 6 L160 14 L240 4 L320 12 L400 6 L480 14 L560 5 L640 13 L720 6 L800 14 L880 5 L960 12 L1040 6 L1120 14 L1200 8 V30 Z"/>
  </svg>
  <div class="abs" style="left:195px;top:40px;width:120px;height:120px;border-radius:50%;background:var(--white);display:flex;align-items:center;justify-content:center">
    <span class="brand-name" style="font-size:19px">RIDGEVOLT</span>
  </div>
  <nav class="footer-nav">
    <span style="left:350px">HOME</span>
    <span style="left:420px">ABOUT US</span>
    <span style="left:514px">WHAT WE OFFER</span>
    <span style="left:653px">BOOKINGS</span>
    <span style="left:752px">CONTACT US</span>
  </nav>
  <p class="abs" style="left:350px;top:108px;font-size:11.5px;color:var(--muted)">© 2018 Company Name&nbsp; All right reserved</p>
  <span class="social" style="left:891px"></span>
  <span class="social" style="left:925px"></span>
  <span class="social" style="left:959px"></span>
  <span class="social" style="left:993px"></span>
</footer>

</body>
</html>
```